Business Card Design

I am an Event and Wedding Planner in need of an eye catching business card featuring my logo (attached), my contact details, and my company tagline (Making every celebration glow with wonder...) I would like the tagline in font similar the logo's font.
Updates
I have just noticed that my logo has a misspelling so for the final design, I will be uploading a corrected logo as soon as I have it.
My apologies.
Reason: Waiting on a corrected logo...Lantern is misspelled and it should say Weddings not Wedding
The logo has been corrected so now Lantern is spelled correctly and it says Weddings instead of Wedding. Please use Edwardian Script ITC as the font for the tagline so it will match the logo. Thank you for your patience.
Target Market(s)
Engaged couples and people hosting milestone celebrations. 25-50 years old, predominately female
Industry/Entity Type
Business
Contact Information for Business Card
Rosalind Merrow, Event Manager / Owner, Mobile: 0491 868 254, Email: rosalind@velvetlanternco.com.au, www.velvetlanternco.com.au, Making every celebration glow with wonder...

```html
<!DOCTYPE html>
<html lang="en">
<head>
<meta charset="utf-8">
<title>Velvet Lantern – Business Card</title>
<link rel="stylesheet" href="https://fonts.googleapis.com/css2?family=Arimo&family=Cormorant+Garamond:ital,wght@1,500&family=Pinyon+Script&display=swap">
<style>
  :root {
    --backdrop: #1f6a1a;
    --card: #ffffff;
    --ink: #1a1a1a;
    --accent-red: #c4161c;
    --forest: #1b3a1b;
  }
  * { margin: 0; padding: 0; box-sizing: border-box; }
  html, body { width: 1200px; height: 1000px; overflow: hidden; }
  body { background: var(--backdrop); position: relative; font-family: "Arimo", Arial, sans-serif; }

  .card {
    position: absolute;
    background: var(--card);
    border-radius: 18px;
    box-shadow: 3px 4px 8px rgba(0,0,0,.35);
    overflow: hidden;
  }

  /* Front face */
  .card-front { left: 92px; top: 30px; width: 750px; height: 440px; }
  .brand {
    position: absolute; left: 0; right: 0; top: 132px;
    display: flex; justify-content: center; align-items: center; gap: 18px;
  }
  .brand-name {
    font-family: "Arimo", Arial, sans-serif;
    font-weight: 400;
    font-size: 50px;
    line-height: 1;
    color: var(--ink);
  }
  .brand-dot {
    width: 26px; height: 26px; border-radius: 50%;
    background: var(--accent-red);
  }
  .shade-band {
    position: absolute; left: 40px; right: 0; top: 296px; height: 22px;
    background: linear-gradient(90deg, rgba(27,58,27,0) 0%, var(--forest) 35%, var(--forest) 55%, rgba(27,58,27,.35) 85%, rgba(27,58,27,0) 100%);
  }
  .tagline-rule {
    position: absolute; left: 110px; width: 560px; top: 365px; height: 1px;
    background: linear-gradient(90deg, rgba(196,22,28,0), var(--accent-red) 40%, rgba(196,22,28,0));
  }
  .tagline {
    position: absolute; left: 0; right: 0; top: 372px;
    text-align: center;
    font-family: "Pinyon Script", cursive;
    font-size: 25px; color: var(--accent-red);
  }

  /* Back face */
  .card-back { left: 338px; top: 494px; width: 776px; height: 470px; }
  .person { position: absolute; left: 15px; top: 27px; }
  .person-name { font-size: 20px; color: var(--accent-red); letter-spacing: .3px; line-height: 1; }
  .person-title {
    font-family: "Cormorant Garamond", Georgia, serif; font-style: italic; font-weight: 500;
    font-size: 17px; color: var(--accent-red); line-height: 1.2;
  }
  .person-bar { width: 183px; height: 9px; background: var(--forest); margin-top: 5px; }
  .contact-rule {
    position: absolute; left: 20px; width: 460px; top: 182px; height: 1px;
    background: linear-gradient(90deg, var(--accent-red), rgba(196,22,28,.2));
  }
  .icon-strip {
    position: absolute; left: 20px; top: 198px; width: 36px; height: 110px;
    background: var(--forest);
  }
  .icon-strip svg { position: absolute; left: 5px; width: 26px; height: 24px; }
  .contact-list { position: absolute; left: 69px; top: 204px; list-style: none; }
  .contact-list li { font-size: 19px; color: var(--accent-red); line-height: 33px; }
</style>
</head>
<body>

<section class="card card-front">
  <div class="brand">
    <span class="brand-name">Velvet Lantern</span>
    <span class="brand-dot" aria-hidden="true"></span>
  </div>
  <div class="shade-band"></div>
  <div class="tagline-rule"></div>
  <p class="tagline">Making every celebration glow with wonder...</p>
</section>

<section class="card card-back">
  <div class="person">
    <div class="person-name">ROSALIND MERROW</div>
    <div class="person-title">Event Manager / Owner</div>
    <div class="person-bar"></div>
  </div>

  <div class="contact-rule"></div>

  <div class="icon-strip">
    <svg style="top:8px" viewBox="0 0 26 24" aria-hidden="true">
      <rect x="1" y="4" width="24" height="16" fill="#c4161c"/>
      <polyline points="1,4 13,14 25,4" fill="none" stroke="#1b3a1b" stroke-width="1.6"/>
    </svg>
    <svg style="top:42px" viewBox="0 0 26 24" aria-hidden="true">
      <path d="M2 8 Q13 0 24 8 L21 11 L17 9 L17 7 Q13 5 9 7 L9 9 L5 11 Z" fill="#c4161c"/>
      <rect x="4" y="12" width="18" height="10" rx="2" fill="#c4161c"/>
      <circle cx="13" cy="17" r="3" fill="#1b3a1b"/>
    </svg>
    <svg style="top:76px" viewBox="0 0 26 24" aria-hidden="true">
      <g fill="none" stroke="#c4161c" stroke-width="1.6">
        <circle cx="13" cy="12" r="10"/>
        <ellipse cx="13" cy="12" rx="4.5" ry="10"/>
        <line x1="3" y1="12" x2="23" y2="12"/>
        <line x1="13" y1="2" x2="13" y2="22"/>
        <path d="M5 6.5 H21 M5 17.5 H21"/>
      </g>
    </svg>
  </div>

  <ul class="contact-list">
    <li>rosalind@velvetlanternco.com.au</li>
    <li>0491 868 254</li>
    <li>www.velvetlanternco.com.au</li>
  </ul>
</section>

</body>
</html>
```